Business card for medical clinic

I need an upmarket, modern medical/health business card for my clinic

Contact Information for Business Card

name, address, email, qr code

```html
<!DOCTYPE html>
<html lang="en">
<head>
<meta charset="utf-8">
<title>Meridel Care Group – Business Card</title>
<link rel="stylesheet" href="https://fonts.googleapis.com/css2?family=Poppins:wght@300;400;600&display=swap">
<style>
  :root {
    --bg: #232323;
    --card: #1a1a1b;
    --card-edge: #111112;
    --blue: #2a9fd8;
    --blue-deep: #1d7fb5;
    --blue-soft: #8fc9ea;
    --ink: #f2f2f2;
    --pattern-a: #1c1c1e;
    --pattern-b: #2a2c30;
  }
  html, body {
    margin: 0; padding: 0;
    width: 1200px; height: 780px;
    overflow: hidden;
    background: var(--bg);
    font-family: "Poppins", sans-serif;
  }
  .canvas {
    position: relative;
    width: 1200px; height: 780px;
    display: flex; align-items: center; justify-content: center;
    gap: 40px;
  }
  .card {
    position: relative;
    width: 540px; height: 309px;
    background: var(--card);
    border-radius: 18px;
    overflow: hidden;
    box-shadow: 0 18px 40px rgba(0,0,0,.45);
  }

  /* Front */
  .brand {
    position: absolute; left: 36px; top: 44px;
    display: flex; align-items: center; gap: 10px;
    color: var(--blue);
    font-weight: 400; font-size: 17px; letter-spacing: 2px;
  }
  .brand-dot {
    width: 14px; height: 14px; border-radius: 50%;
    background: var(--blue);
  }
  .divider {
    position: absolute; left: 0; top: 0;
    width: 540px; height: 309px;
  }
  .person {
    position: absolute; left: 312px; top: 70px;
  }
  .person-name {
    margin: 0;
    font-size: 27px; line-height: 1.1;
    color: var(--blue);
  }
  .person-name .first { font-weight: 600; }
  .person-name .last { font-weight: 300; }
  .person-title {
    margin: 4px 0 18px;
    font-size: 12px; color: var(--ink); font-weight: 400;
  }
  .contact-list { list-style: none; margin: 0; padding: 0; }
  .contact-list li {
    display: flex; align-items: center; gap: 9px;
    font-size: 12.5px; color: var(--ink);
    margin-bottom: 6px;
  }
  .contact-list svg { width: 13px; height: 13px; flex: none; }
  .address {
    position: absolute; left: 36px; bottom: 30px;
    margin: 0;
    font-size: 12px; color: var(--blue);
  }
  .edge-band {
    position: absolute; bottom: 0; height: 8px;
    background: linear-gradient(90deg, var(--blue-deep), var(--blue));
  }
  .edge-band.left { left: 0; width: 150px; }
  .edge-band.right { left: 162px; right: 0; }

  /* Back */
  .card-back { background: var(--card-edge); }
  .back-pattern {
    position: absolute; inset: 0;
    background: radial-gradient(circle at 75% 70%, var(--pattern-b), var(--pattern-a) 70%);
  }
  .back-brand {
    position: absolute; left: 0; right: 0; top: 50%;
    transform: translateY(-50%);
    display: flex; align-items: center; justify-content: center; gap: 12px;
    color: var(--blue);
    font-size: 24px; font-weight: 400; letter-spacing: 3px;
  }
  .back-brand .brand-dot { width: 18px; height: 18px; }
</style>
</head>
<body>
<main class="canvas">

  <section class="card card-front" aria-label="Business card front">
    <div class="brand">
      <span class="brand-dot"></span>
      <span class="brand-name">MERIDEL CARE</span>
    </div>

    <svg class="divider" viewBox="0 0 540 309" aria-hidden="true">
      <line x1="282" y1="232" x2="300" y2="58" stroke="var(--blue-deep)" stroke-width="1"/>
    </svg>

    <div class="person">
      <h1 class="person-name"><span class="first">Lena</span> <span class="last">Marsh</span></h1>
      <p class="person-title">Founder &amp; CEO</p>
      <ul class="contact-list">
        <li>
          <svg viewBox="0 0 16 16" aria-hidden="true"><path d="M4 1.5l2.5 3-1.5 1.8c.8 1.8 2.1 3.1 3.9 3.9l1.8-1.5 3 2.5-1.6 2.5C7 13.5 2.5 9 1.5 3.1z" fill="var(--blue)"/></svg>
          (555) 014-2290
        </li>
        <li>
          <svg viewBox="0 0 16 16" aria-hidden="true"><rect x="1.5" y="3.5" width="13" height="9" rx="1" fill="none" stroke="var(--blue)" stroke-width="1.4"/><path d="M1.5 4l6.5 5 6.5-5" fill="none" stroke="var(--blue)" stroke-width="1.4"/></svg>
          info@meridelcare.com
        </li>
        <li>
          <svg viewBox="0 0 16 16" aria-hidden="true"><circle cx="8" cy="8" r="6.5" fill="none" stroke="var(--blue)" stroke-width="1.4"/><path d="M1.5 8h13M8 1.5c2.2 2 2.2 11 0 13M8 1.5c-2.2 2-2.2 11 0 13" fill="none" stroke="var(--blue)" stroke-width="1.2"/></svg>
          www.meridelcare.com
        </li>
      </ul>
    </div>

    <p class="address">480 Linden Ave. Suite 120 Fairview, TX 75010</p>
    <span class="edge-band left"></span>
    <span class="edge-band right"></span>
  </section>

  <section class="card card-back" aria-label="Business card back">
    <div class="back-pattern" role="img" aria-label="Embossed repeating ring pattern in glossy black"></div>
    <div class="back-brand">
      <span class="brand-dot"></span>
      <span class="brand-name">MERIDEL CARE</span>
    </div>
  </section>

</main>
</body>
</html>
```